Northfield Builders Guild Business card

We are looking for a new business card design with photo included.
Our business is a nonprofit construction contractor membership organization. We offer business education, assist with business setup and licensing, provide safety training, and provide a member directory.
URL: www.builderslinkguild.org
Color code:
CMYK: 0 cyan, 42 magenta, 100 yellow, 0 black for Print.
Hexidecimal: #FF9900
RGB: R 255; G 153; B 0

```html
<!DOCTYPE html>
<html lang="en">
<head>
<meta charset="utf-8">
<title>Northfield Builders Guild – Business Card</title>
<link href="https://fonts.googleapis.com/css2?family=Arimo:wght@400;700&display=swap" rel="stylesheet">
<style>
  :root {
    --orange: #ff9900;
    --card: #0b0b0b;
    --white: #ffffff;
    --rule: #3a3a3a;
    --steel: #b8b8b8;
    --backdrop: #2a2624;
  }
  * { margin: 0; padding: 0; box-sizing: border-box; }
  html, body { width: 1200px; height: 842px; overflow: hidden; }
  body {
    background: var(--backdrop);
    font-family: "Arimo", Arial, sans-serif;
    display: flex;
    align-items: center;
    justify-content: center;
    gap: 40px;
  }
  .card {
    position: relative;
    width: 540px;
    height: 309px;
    background: var(--card);
    overflow: hidden;
    box-shadow: 0 12px 30px rgba(0,0,0,.5);
  }

  /* Contact side */
  .band { position: absolute; left: 0; right: 0; height: 12px; background: var(--orange); }
  .band--top { top: 0; }
  .band--bottom { bottom: 0; }
  .contact {
    position: absolute; inset: 0;
    display: flex; flex-direction: column; align-items: center; justify-content: center;
    text-align: center; color: var(--white); font-size: 13px; line-height: 1.3;
  }
  .contact__name { color: var(--orange); font-weight: 700; font-size: 17px; letter-spacing: .5px; }
  .contact__title { font-size: 11px; letter-spacing: .6px; }
  .contact__rule { width: 130px; height: 1px; background: var(--rule); margin: 9px 0; }
  .label { color: var(--orange); }
  .contact__org { color: var(--orange); }

  /* Brand side */
  .tab { position: absolute; width: 34px; height: 48px; background: var(--orange); }
  .tab--left { left: 0; top: 196px; border-right: 5px solid var(--steel); }
  .tab--right { right: 0; top: 40px; border-left: 5px solid var(--steel); }
  .brand {
    position: absolute; inset: 0;
    display: flex; flex-direction: column; align-items: center; justify-content: center;
  }
  .brand__name {
    color: var(--white); font-weight: 700; font-size: 30px; text-transform: uppercase;
    text-align: center; line-height: 1.1; letter-spacing: 1px;
  }
  .brand__url { margin-top: 34px; color: var(--white); font-size: 12px; }
  .brand__url .accent { color: var(--orange); }
</style>
</head>
<body>
  <section class="card card--contact">
    <div class="band band--top"></div>
    <div class="contact">
      <div class="contact__name">MARCUS HALE</div>
      <div class="contact__title">MANAGING DIRECTOR</div>
      <div class="contact__rule"></div>
      <div><span class="label">Office:</span> (555) 314-2710</div>
      <div><span class="label">Phone:</span> 800-555-0147</div>
      <div><span class="label">Fax:</span> 555.208.0193</div>
      <div><span class="label">Email:</span> support@nbguild.org</div>
      <div class="contact__rule"></div>
      <div class="contact__org">Northfield Builders Guild</div>
      <div>2400 Alder Ridge Rd.,</div>
      <div>Suite #210, Fairview, OR 97024</div>
    </div>
    <div class="band band--bottom"></div>
  </section>

  <section class="card card--brand">
    <div class="tab tab--right"></div>
    <div class="tab tab--left"></div>
    <div class="brand">
      <div class="brand__name">Northfield<br>Builders Guild</div>
      <div class="brand__url">www.<span class="accent">builderslinkguild</span>.org</div>
    </div>
  </section>
</body>
</html>
```